Brell Stone Company Business Cards

Front and Back Business Card - logo and text setup - cool design. I need workable photoshop or illustrator files so I can setup each employee card with design that is created
Updates

Hi everyone, thank you for the great entries. Please no more white and blue cards - there are so many already - black and silver only now please. thanks!

Target Market(s)

Construction Industry - Facility Managers

Industry/Entity Type

Construction

Contact Information for Business Card

I really like contemporary simplistic looks - clean neat....not opposed to seeing some black backrounds

Requirements
Must have
• Logo/website address with design on front only - www.brellstone-example.com (logo attached)
• Back:
• Name/Title/Company Address/Phone/email address
Nice to have
• Cool design
Should not have
• Nothing gimmicky like Fire or Water - since we are a Fire Protection company - it has all been done

```html
<!DOCTYPE html>
<html lang="en">
<head>
<meta charset="utf-8">
<title>Brell Stone Company – Business Cards</title>
<link rel="stylesheet" href="https://fonts.googleapis.com/css2?family=Source+Sans+3:wght@400;600;700&display=swap">
<style>
  :root {
    --stage-light: #e8e9ea;
    --stage-dark: #cfd0d2;
    --card-white: #ffffff;
    --ink: #231f20;
    --ink-soft: #3a3a3a;
    --band-dark: #242223;
    --band-mid: #2e2c2d;
    --band-light: #3f3e40;
    --back-center: #3b3a3c;
    --back-edge: #1f1d1e;
    --paper-white: #ffffff;
  }
  * { margin: 0; padding: 0; box-sizing: border-box; }
  html, body { width: 800px; height: 1200px; overflow: hidden; }
  body {
    position: relative;
    background: radial-gradient(ellipse at 50% 50%, var(--stage-light) 0%, var(--stage-dark) 85%);
    font-family: "Source Sans 3", "Myriad Pro", Arial, sans-serif;
    color: var(--ink);
  }
  .card {
    position: absolute;
    width: 504px;
    height: 288px;
    overflow: hidden;
  }
  .card--front { left: 148px; top: 174px; background: var(--card-white); }
  .card--back {
    left: 118px; top: 703px;
    background: radial-gradient(ellipse at 50% 45%, var(--back-center) 0%, var(--back-edge) 75%);
  }
  .front-shapes { position: absolute; left: 0; top: 0; width: 504px; height: 288px; }

  .brand {
    position: absolute;
    display: flex;
    align-items: center;
    gap: 8px;
    font-weight: 700;
    white-space: nowrap;
  }
  .brand__mark { display: block; flex: none; }
  .card--front .brand {
    right: 24px; top: 34px;
    font-size: 30px; line-height: 1;
    color: var(--ink);
  }
  .card--front .brand__mark { width: 14px; height: 14px; background: var(--ink); }

  .holder { position: absolute; left: 18px; top: 84px; }
  .holder__name { font-size: 23px; font-weight: 600; line-height: 1; letter-spacing: -0.2px; }
  .holder__title { margin-top: 3px; margin-left: 2px; font-size: 13px; font-weight: 400; color: var(--ink-soft); }

  .contact {
    position: absolute;
    right: 20px; top: 128px;
    list-style: none;
    text-align: right;
  }
  .contact__item {
    display: flex; justify-content: flex-end; align-items: center;
    gap: 9px;
    height: 29px;
    font-size: 13px; color: var(--ink-soft);
  }
  .contact__icon { width: 10px; height: 11px; fill: var(--ink-soft); flex: none; }

  .card--back .brand {
    left: 0; right: 0; top: 116px;
    justify-content: center;
    font-size: 40px; line-height: 1;
    color: var(--paper-white);
  }
  .card--back .brand__mark { width: 16px; height: 16px; background: var(--paper-white); }
  .website {
    position: absolute; left: 0; right: 0; top: 197px;
    text-align: center;
    font-size: 14px; color: var(--paper-white);
  }
</style>
</head>
<body>

  <section class="card card--front" aria-label="Business card front">
    <svg class="front-shapes" viewBox="0 0 630 360" preserveAspectRatio="none" aria-hidden="true">
      <defs>
        <linearGradient id="barShade" x1="0" x2="1" y1="0" y2="0">
          <stop offset="0" stop-color="var(--band-mid)"/>
          <stop offset="1" stop-color="var(--band-light)"/>
        </linearGradient>
      </defs>
      <polygon points="260,275 630,275 630,306 288,306" fill="var(--band-dark)"/>
      <rect x="0" y="305" width="630" height="50" fill="url(#barShade)"/>
      <polygon points="0,211 72,280 115,280 140,305 0,305" fill="var(--band-mid)"/>
      <polygon points="0,211 150,355 0,355" fill="var(--band-dark)"/>
    </svg>

    <div class="brand"><span class="brand__mark"></span>Brell Stone</div>

    <div class="holder">
      <h1 class="holder__name">Martin Keller</h1>
      <p class="holder__title">Managing Member</p>
    </div>

    <ul class="contact">
      <li class="contact__item">0300-555-014
        <svg class="contact__icon" viewBox="0 0 10 11"><path d="M2 0.5 L4 2.8 L3 4 C3.6 5.6 4.8 7 6.3 7.8 L7.5 6.8 L9.8 8.8 L8.6 10.4 C4.8 10.2 0.4 5.6 0.4 1.8 Z"/></svg>
      </li>
      <li class="contact__item">@yourweb.com
        <svg class="contact__icon" viewBox="0 0 10 11"><rect x="0.5" y="3" width="9" height="6.5"/><path d="M0.8 3.3 L5 6.6 L9.2 3.3" fill="none" stroke="#fff" stroke-width="0.8"/></svg>
      </li>
      <li class="contact__item">your address here
        <svg class="contact__icon" viewBox="0 0 10 11"><path d="M5 0.3 C7.4 0.3 9 2 9 4 C9 6.6 5 10.8 5 10.8 C5 10.8 1 6.6 1 4 C1 2 2.6 0.3 5 0.3 Z M5 2.6 A1.4 1.4 0 1 0 5.01 2.6 Z" fill-rule="evenodd"/></svg>
      </li>
    </ul>
  </section>

  <section class="card card--back" aria-label="Business card back">
    <div class="brand"><span class="brand__mark"></span>Brell Stone</div>
    <p class="website">www.brellstone-example.com</p>
  </section>

</body>
</html>
```